Corvane Business Cards

Front of business card will have logo, name, address, & telephone number. Back of card will have a list of services provided - Roads, Substation Pads, Temporary Pads, Site Pads, Land Leveling, Powerline Row Cleaning, Land Clearing, Gates, Fencing, Construction Entrances, Excavation, Trenching, Underground Utilities, Directional Boring, Pile Driving. We are a construction company that uses heavy equipment like bulldozers, motor graders/blades, dump trucks, backhoes, hydro axes, & skid loaders. We build roads, pads, & install electric utility lines & waterlines underground. This logo is new. The word "Construction" can be smaller as uploaded 2 example edited logos. We will be using this card design for many employees.
Target Market(s)
Industrial Electric Powerline, Wind Turbine, Solar Panel, & Water Utility companies.
Contact Information for Business Card
Name/Position - Dwayne Halster - Owner
Address: 4875 FM 309
Ridgemoor, KS 67412
Phone number - (325) 482-5096

```html
<!DOCTYPE html>
<html lang="en">
<head>
<meta charset="UTF-8">
<title>Corvane Business Cards</title>
<link href="https://fonts.googleapis.com/css2?family=Poppins:wght@400;500;600&display=swap" rel="stylesheet">
<style>
  :root {
    --backdrop: #a4a4a4;
    --maroon: #3a0b15;
    --maroon-deep: #300811;
    --paper: #e4e4e7;
    --ink-light: #ececec;
  }
  * { margin: 0; padding: 0; box-sizing: border-box; }
  html, body { width: 1105px; height: 1200px; overflow: hidden; }
  body {
    background: var(--backdrop);
    font-family: "Poppins", sans-serif;
    position: relative;
  }
  .card {
    position: absolute;
    left: 182px;
    width: 746px;
    height: 426px;
    overflow: hidden;
  }
  .card-front { top: 120px; background: var(--maroon); }
  .card-back { top: 638px; background: var(--maroon-deep); }

  .front-panel { position: absolute; inset: 0; }

  .contact-block {
    position: absolute;
    left: 58px;
    top: 124px;
    color: var(--ink-light);
  }
  .person-name {
    font-size: 20px;
    font-weight: 600;
    letter-spacing: 0.3px;
    line-height: 1.2;
  }
  .person-role {
    font-size: 15px;
    line-height: 1.3;
    margin-bottom: 16px;
  }
  .address-line { font-size: 15px; line-height: 1.42; }
  .address { margin-bottom: 14px; }
  .contact-row {
    display: flex;
    align-items: center;
    gap: 8px;
    font-size: 15.5px;
    line-height: 1.4;
  }
  .contact-row svg { width: 12px; height: 12px; flex: none; fill: var(--ink-light); }

  .brand-front {
    position: absolute;
    left: 450px;
    width: 260px;
    top: 168px;
    text-align: center;
    color: var(--maroon);
    font-weight: 600;
    line-height: 1.1;
  }
  .brand-front .brand-name { font-size: 52px; letter-spacing: 1px; }
  .brand-front .brand-sub { font-size: 22px; letter-spacing: 0.5px; margin-top: 6px; }

  .brand-back {
    position: absolute;
    left: 0; right: 0;
    top: 140px;
    text-align: center;
    color: var(--paper);
    font-weight: 600;
    font-size: 84px;
    letter-spacing: 3px;
    line-height: 1;
  }
  .service-list {
    position: absolute;
    left: 0; right: 0;
    top: 340px;
    text-align: center;
    color: var(--ink-light);
    font-size: 15.5px;
    line-height: 1.32;
  }
</style>
</head>
<body>

<section class="card card-front">
  <svg class="front-panel" viewBox="0 0 746 426" width="746" height="426" aria-hidden="true">
    <path fill="var(--paper)" d="M318,0 C368,0 386,60 395,150 C404,240 440,330 376,426 L746,426 L746,0 Z"/>
    <path fill="var(--paper)" d="M366,238 C406,282 412,350 393,408 C402,345 396,286 366,238 Z"/>
  </svg>

  <div class="contact-block">
    <p class="person-name">DWAYNE HALSTER</p>
    <p class="person-role">Owner</p>
    <div class="address">
      <p class="address-line">4875 FM 309</p>
      <p class="address-line">Ridgemoor, KS 67412</p>
    </div>
    <p class="contact-row">
      <svg viewBox="0 0 24 24"><path d="M6.6 10.8a15.1 15.1 0 0 0 6.6 6.6l2.2-2.2c.3-.3.7-.4 1-.2 1.1.4 2.3.6 3.6.6.6 0 1 .4 1 1V20c0 .6-.4 1-1 1C10.6 21 3 13.4 3 4c0-.6.4-1 1-1h3.5c.6 0 1 .4 1 1 0 1.3.2 2.5.6 3.6.1.3 0 .7-.2 1z"/></svg>
      (325) 482-5096
    </p>
    <p class="contact-row">
      <svg viewBox="0 0 24 24"><path d="M2 5h20v14H2z M4 7v.5l8 5 8-5V7z" fill-rule="evenodd"/></svg>
      info@corvaneconstruction.com
    </p>
    <p class="contact-row">
      <svg viewBox="0 0 24 24"><circle cx="12" cy="12" r="10"/></svg>
      www.corvaneconstruction.com
    </p>
  </div>

  <div class="brand-front">
    <p class="brand-name">CORVANE</p>
    <p class="brand-sub">CONSTRUCTION</p>
  </div>
</section>

<section class="card card-back">
  <p class="brand-back">CORVANE</p>
  <div class="service-list">
    <p>Roads • Substation Pads•Temporary Pads • Site Pads • Land Leveling</p>
    <p>Powerline Row Cleaning • Land Clearing • Gates • Fencing • Construction Entrances</p>
    <p>Excavation • Trenching • Underground Utilities • Directional Boring • Pile Driving</p>
  </div>
</section>

</body>
</html>
```